Design eines Hausetiketts für traditionelles Weingut
Zielgruppe
Wir das Familienweingut Brandauer in Gimbsheim/Rheinhessen sind ein traditionelles Weingut das seine Reben selbst kultiviert und die Weine auch selbst ausbaut. Wir haben jeden Schritt in der Weinherstellung selbst in der Hand und vermarkten den Wein dann an unsere Privatkunden. Unsere Kundenstruktur sieht folgendermaßen aus: Wir haben 100% Privatkunden die unseren Wein konsumieren. Da jetzt die nächste Generation in den Weinbaubetrieb einsteigt und auch Ideen hat möchten wir ein Hausetikett einführen. Im Moment haben wir noch sehr viele unterschiedliche Etiketten und kein Hausetikett. Da die Verlagsetiketten immer seltener zu unseren Vorstellungen passen, möchten wir hier auf diesem Wege ein Hausetikett anfertigen lassen. Generell möchten wir unseren Außenauftritt komplett modernisieren. Sie können sich über die Vielfalt in unserem Betrieb unter www.weingut-brandauer-beispiel.de einen Überblick verschaffen. Langfristig gesehen wollen wir aber unsere Weinkarte verkleinern.
Aufgabenstellung
Wir haben uns vor ca. 1,5 Jahren hier auf dieser Website bereits ein Logo designen lassen. Es wäre schön wenn man das Logo bei den Entwürfen für die Etiketten berücksichtigen würde. Das wäre aber KEIN MUSS. Auch wäre es gut wenn man das ,,Wein' bei unserem Namen weglassen könnte.
Das Etikett sollte aus Vorder-und Rückenetikett bestehen und edel wirken. Vorne sollte die Rebsorte und die Geschmacksangabe stehen. Der Rest sollte auf das Rückenetikett.
Das Vorderetikett sollte ein richtiger Eyecatcher sein und im Supermarkt z.B. aus vielen anderen herausstechen. Das wäre ganz wichtig.
Man kann bei den Farben unterscheiden in 3 Konzepte.
Literwein als einsteiger Wein
Dann die Gutsweine und zum Schluss die Lagenweine. Alles Farblich oder im design etwas abgesetzt.

```html
<!DOCTYPE html>
<html lang="de">
<head>
<meta charset="utf-8">
<title>Brandauer Hausetikett – Entwürfe</title>
<link rel="stylesheet" href="https://fonts.googleapis.com/css2?family=Bebas+Neue&family=Marcellus&display=swap">
<style>
  :root{
    --sheet:#dcdedd;
    --sheet-edge:#8f9291;
    --ink:#2a2727;
    --wine-red:#e31e24;
    --riesling:#fdf08a;
    --gold:#e9c08f;
    --page:#ffffff;
    --olive:#6e6c18;
    --maroon:#5c1b2c;
  }
  html,body{margin:0;padding:0;overflow:hidden;}
  body{width:1200px;height:3127px;background:var(--page);position:relative;}
  .sheet{position:absolute;background:var(--sheet);border:1px solid var(--sheet-edge);box-sizing:border-box;}
  .stage{position:absolute;}
  .stage--riesling{background:var(--olive);}
  .stage--dornfelder{background:var(--maroon);}

  .label{position:absolute;overflow:hidden;container-type:inline-size;}
  .label--dark{background:var(--ink);}
  .label--red{background:var(--wine-red);}
  .label--yellow{background:var(--riesling);}

  .label__texture{position:absolute;left:0;right:0;top:22%;height:48%;}
  .label__texture-strip{position:absolute;right:0;width:26%;bottom:0;height:5%;}

  .tex--red-on-dark{background:linear-gradient(160deg,rgba(227,30,36,.85) 0%,rgba(42,39,39,.6) 35%,rgba(227,30,36,.8) 60%,rgba(42,39,39,0) 100%);}
  .tex--dark-on-red{background:linear-gradient(160deg,rgba(42,39,39,.85) 0%,rgba(227,30,36,.5) 35%,rgba(42,39,39,.8) 60%,rgba(227,30,36,0) 100%);}
  .tex--dark-on-yellow{background:linear-gradient(160deg,rgba(42,39,39,.8) 0%,rgba(253,240,138,.5) 35%,rgba(42,39,39,.7) 60%,rgba(253,240,138,0) 100%);}
  .tex--yellow-on-dark{background:linear-gradient(160deg,rgba(253,240,138,.85) 0%,rgba(42,39,39,.5) 35%,rgba(253,240,138,.75) 60%,rgba(42,39,39,0) 100%);}

  .label__brand{position:absolute;left:0;right:0;top:9%;text-align:center;
    font-family:"Marcellus",serif;font-size:13.5cqw;line-height:1;letter-spacing:-.02em;margin:0;font-weight:400;}

  .label__style{position:absolute;left:6%;margin:0;font-family:"Marcellus",serif;font-weight:400;}
  .label__style--red{top:72.5%;font-size:6.2cqw;line-height:.9;}
  .label__style--white{top:76.8%;font-size:6.4cqw;line-height:1;}

  .label__variety{position:absolute;margin:0;font-family:"Bebas Neue",sans-serif;font-weight:400;}
  .label__variety--red{left:6%;top:80.8%;font-size:15.6cqw;line-height:.84;}
  .label__variety--white{left:4.5%;top:85.6%;font-size:20.5cqw;line-height:.9;}

  .c-red{color:var(--wine-red);}
  .c-ink{color:var(--ink);}
  .c-yellow{color:var(--riesling);}
  .c-gold{color:var(--gold);}
</style>
</head>
<body>

  <section class="sheet" style="left:30px;top:0;width:1118px;height:944px;">
    <article class="label label--dark" style="left:12px;top:40px;width:526px;height:866px;">
      <div class="label__texture tex--red-on-dark" role="img" aria-label="Rote Marmor-Farbschlieren"></div>
      <div class="label__texture-strip tex--red-on-dark" role="img" aria-label="Rote Farbschliere"></div>
      <h1 class="label__brand c-red">BRANDAUER</h1>
      <p class="label__style label__style--red c-red">ROTWEIN<br>HALBTROCKEN</p>
      <h2 class="label__variety label__variety--red c-red">DORNFELDER<br>ROTWEIN</h2>
    </article>
    <article class="label label--red" style="left:552px;top:40px;width:526px;height:866px;">
      <div class="label__texture tex--dark-on-red" role="img" aria-label="Dunkle Marmor-Farbschlieren"></div>
      <div class="label__texture-strip tex--dark-on-red" role="img" aria-label="Dunkle Farbschliere"></div>
      <h1 class="label__brand c-ink">BRANDAUER</h1>
      <p class="label__style label__style--red c-ink">ROTWEIN<br>HALBTROCKEN</p>
      <h2 class="label__variety label__variety--red c-ink">DORNFELDER<br>ROTWEIN</h2>
    </article>
  </section>

  <section class="sheet" style="left:24px;top:1011px;width:1123px;height:941px;">
    <article class="label label--yellow" style="left:41px;top:39px;width:526px;height:865px;">
      <div class="label__texture tex--dark-on-yellow" role="img" aria-label="Dunkle Marmor-Farbschlieren"></div>
      <div class="label__texture-strip tex--dark-on-yellow" role="img" aria-label="Dunkle Farbschliere"></div>
      <h1 class="label__brand c-ink">BRANDAUER</h1>
      <p class="label__style label__style--white c-ink">WEISSWEIN<br>&nbsp;TROCKEN</p>
      <h2 class="label__variety label__variety--white c-ink">RIESLING</h2>
    </article>
    <article class="label label--dark" style="left:580px;top:39px;width:526px;height:865px;">
      <div class="label__texture tex--yellow-on-dark" role="img" aria-label="Gelbe Marmor-Farbschlieren"></div>
      <div class="label__texture-strip tex--yellow-on-dark" role="img" aria-label="Gelbe Farbschliere"></div>
      <h1 class="label__brand c-gold">BRANDAUER</h1>
      <p class="label__style label__style--white c-yellow">WEISSWEIN<br>&nbsp;TROCKEN</p>
      <h2 class="label__variety label__variety--white c-yellow">RIESLING</h2>
    </article>
  </section>

  <section class="stage stage--riesling" style="left:15px;top:2010px;width:566px;height:1090px;">
    <article class="label label--dark" style="left:133px;top:300px;width:300px;height:493px;">
      <div class="label__texture tex--yellow-on-dark" role="img" aria-label="Gelbe Marmor-Farbschlieren"></div>
      <div class="label__texture-strip tex--yellow-on-dark" role="img" aria-label="Gelbe Farbschliere"></div>
      <h1 class="label__brand c-gold">BRANDAUER</h1>
      <p class="label__style label__style--white c-yellow">WEISSWEIN<br>&nbsp;TROCKEN</p>
      <h2 class="label__variety label__variety--white c-yellow">RIESLING</h2>
    </article>
  </section>

  <section class="stage stage--dornfelder" style="left:596px;top:2016px;width:555px;height:1078px;">
    <article class="label label--dark" style="left:127px;top:300px;width:300px;height:493px;">
      <div class="label__texture tex--red-on-dark" role="img" aria-label="Rote Marmor-Farbschlieren"></div>
      <div class="label__texture-strip tex--red-on-dark" role="img" aria-label="Rote Farbschliere"></div>
      <h1 class="label__brand c-red">BRANDAUER</h1>
      <p class="label__style label__style--red c-red">ROTWEIN<br>HALBTROCKEN</p>
      <h2 class="label__variety label__variety--red c-red">DORNFELDER<br>ROTWEIN</h2>
    </article>
  </section>

</body>
</html>
```